Business Card Design Project - 2 sided

We need a business card design for a card having one business on each side (ie. two businesses on one card). Would like a design that incorporates logo, tagline and normal fields (name, position, address, phone).

Would also like an allowance for small font text along the bottom (text to be determined, but less than 50 characters).

NB. Attached logo for Harbor Quill has two variations - either can be used.

www.harborquill-example.com / www.velmaro-example.com

```html
<!DOCTYPE html>
<html lang="en">
<head>
<meta charset="utf-8">
<title>Harbor Quill / Velmaro LLC – Business Card</title>
<link rel="stylesheet" href="https://fonts.googleapis.com/css2?family=Source+Sans+3:wght@400;600;700&display=swap">
<style>
  :root {
    --backdrop: #e8e3dc;
    --card: #ffffff;
    --green: #8cc63f;
    --grey: #6d6e71;
    --blue: #2b86c5;
    --navy: #2b2d6e;
    --ink: #4d4d4f;
    --rule: #9a9a9a;
  }
  * { box-sizing: border-box; margin: 0; padding: 0; }
  html, body { width: 1200px; height: 487px; overflow: hidden; }
  body {
    background: var(--backdrop);
    font-family: "Source Sans 3", sans-serif;
    color: var(--ink);
    position: relative;
  }
  .card {
    position: absolute;
    top: 88px;
    width: 544px;
    height: 310px;
    background: var(--card);
    box-shadow: 0 3px 8px rgba(0,0,0,.25);
  }
  .card--harbor { left: 42px; }
  .card--velmaro { left: 613px; }
  .card__edge { position: absolute; left: 0; top: 0; width: 11px; height: 310px; }
  .card__person {
    position: absolute; left: 350px; top: 50px;
    font-size: 19px; color: var(--green); font-weight: 700; letter-spacing: .2px;
  }
  .card__person .title { font-weight: 400; color: var(--grey); font-size: 15px; }
  .brand { position: absolute; display: flex; flex-direction: column; }
  .brand__row { display: flex; align-items: center; gap: 10px; }
  .brand__dot { width: 26px; height: 26px; border-radius: 50%; background: var(--green); }
  .brand__name { font-size: 30px; font-weight: 600; line-height: 1; }
  .brand__tagline { font-size: 11px; margin-top: 6px; }
  .card--harbor .brand { left: 54px; top: 172px; }
  .card--harbor .brand__name { color: var(--navy); letter-spacing: 1px; }
  .card--harbor .brand__tagline { color: var(--ink); }
  .card--velmaro .brand { left: 52px; top: 72px; }
  .card--velmaro .brand__name { color: var(--blue); font-size: 34px; }
  .card--velmaro .brand__tagline { color: var(--ink); margin-left: 64px; font-size: 12px; letter-spacing: .4px; }
  .contact {
    position: absolute; left: 62px; top: 228px;
    display: flex; font-size: 14px; line-height: 18px;
  }
  .contact__col { padding-right: 12px; }
  .contact__col + .contact__col { border-left: 1px solid var(--rule); padding-left: 10px; }
  .contact__item { display: flex; align-items: center; gap: 6px; }
  .contact__item svg { width: 10px; height: 10px; flex: none; }
  .card__footnote {
    position: absolute; left: 64px; top: 274px;
    font-size: 11px; letter-spacing: .3px; color: var(--ink);
  }
</style>
</head>
<body>

<section class="card card--harbor">
  <svg class="card__edge" viewBox="0 0 11 310" aria-hidden="true">
    <polygon points="0,0 11,0 11,138 0,146" fill="var(--green)"/>
    <polygon points="0,151 11,143 11,310 0,310" fill="var(--grey)"/>
  </svg>
  <div class="brand">
    <div class="brand__row"><span class="brand__dot"></span><span class="brand__name">Harbor Quill</span></div>
    <span class="brand__tagline">Website Translation and Localisation Specialist...</span>
  </div>
  <p class="card__person">YOUR NAME <span class="title">/ Title</span></p>
  <div class="contact">
    <div class="contact__col">
      <p class="contact__item"><svg viewBox="0 0 10 10"><path d="M2 1l2 2-1 1.5a6 6 0 0 0 2.5 2.5L7 6l2 2-1.5 1.5C4 9 1 6 .5 2.5z" fill="var(--green)"/></svg>123-456-7890</p>
      <p class="contact__item"><svg viewBox="0 0 10 10"><rect x="2.5" y="0" width="5" height="10" rx="1" fill="var(--green)"/></svg>123-456-7890</p>
    </div>
    <div class="contact__col">
      <p class="contact__item"><svg viewBox="0 0 10 10"><rect x="0" y="2" width="10" height="7" fill="var(--green)"/><path d="M0 2l5 4 5-4" stroke="#fff" fill="none"/></svg>name@website.com</p>
      <p class="contact__item"><svg viewBox="0 0 10 10"><circle cx="5" cy="5" r="5" fill="var(--green)"/><path d="M0 5h10M5 0v10" stroke="#fff" stroke-width=".8"/></svg>www.website.com</p>
    </div>
    <div class="contact__col">
      <p>Complex name, Street</p>
      <p>City, State, zip code</p>
    </div>
  </div>
  <p class="card__footnote">xxxxxxxxxxxxxxxxxxxxxxxxxxxxxxxxxxxxxxxxxxxxxxxxx</p>
</section>

<section class="card card--velmaro">
  <svg class="card__edge" viewBox="0 0 11 310" aria-hidden="true">
    <polygon points="0,0 11,0 11,138 0,146" fill="var(--green)"/>
    <polygon points="0,151 11,143 11,310 0,310" fill="var(--blue)"/>
  </svg>
  <div class="brand">
    <div class="brand__row"><span class="brand__dot"></span><span class="brand__name">Velmaro LLC</span></div>
    <span class="brand__tagline">Professional SEO Services</span>
  </div>
  <p class="card__person">YOUR NAME <span class="title">/ Title</span></p>
  <div class="contact">
    <div class="contact__col">
      <p class="contact__item"><svg viewBox="0 0 10 10"><path d="M2 1l2 2-1 1.5a6 6 0 0 0 2.5 2.5L7 6l2 2-1.5 1.5C4 9 1 6 .5 2.5z" fill="var(--green)"/></svg>123-456-7890</p>
      <p class="contact__item"><svg viewBox="0 0 10 10"><rect x="2.5" y="0" width="5" height="10" rx="1" fill="var(--green)"/></svg>123-456-7890</p>
    </div>
    <div class="contact__col">
      <p class="contact__item"><svg viewBox="0 0 10 10"><rect x="0" y="2" width="10" height="7" fill="var(--green)"/><path d="M0 2l5 4 5-4" stroke="#fff" fill="none"/></svg>name@website.com</p>
      <p class="contact__item"><svg viewBox="0 0 10 10"><circle cx="5" cy="5" r="5" fill="var(--green)"/><path d="M0 5h10M5 0v10" stroke="#fff" stroke-width=".8"/></svg>www.website.com</p>
    </div>
    <div class="contact__col">
      <p>Complex name, Street</p>
      <p>City, State, zip code</p>
    </div>
  </div>
  <p class="card__footnote">xxxxxxxxxxxxxxxxxxxxxxxxxxxxxxxxxxxxxxxxxxxxxxxxx</p>
</section>

</body>
</html>
```